Indy Film Production Company/Studio

We need a business card designed from an existing logo. We are a digital studio/production company that caters to creating genre entertainment, like Action, Horror, and martial arts. The card along with the logo will be used to Brand the company from letter heads to banners. The design will also be used for postcards and Brochures. It should be professional and masculine.
Updates

Thank you to all the designers who have participated. I'm narrowing down who it will be. Thank you again.

Target Market(s)

Investors, Networks, Producers, and actors

Industry/Entity Type

Film Production

Contact Information for Business Card

Teodoro Valbuena
Producer/Writer/Director
www.kestrelpicturehouse.example

Requirements
Must have
• Website address, Facebook icon and Twitter icon possibly in the back of the card.
Nice to have
• Logline of Company: Follow The Action.

```html
<!DOCTYPE html>
<html lang="en">
<head>
<meta charset="utf-8">
<title>Kestrel Picture House – Business Card</title>
<link href="https://fonts.googleapis.com/css2?family=Roboto:wght@400;500;900&display=swap" rel="stylesheet">
<style>
  :root {
    --page-bg: #2b2b2d;
    --brand-red: #e3171f;
    --brand-red-dark: #b80f16;
    --stripe-grey: #3a3a3c;
    --card-white: #ffffff;
    --card-charcoal: #262628;
    --card-charcoal-light: #3a3a3d;
    --text-grey: #4a4a4a;
    --muted-grey: #9a9a9c;
  }
  * { margin: 0; padding: 0; box-sizing: border-box; }
  html, body {
    width: 1200px; height: 950px; overflow: hidden;
    background: var(--page-bg);
    font-family: "Roboto", Arial, sans-serif;
  }
  .canvas { position: relative; width: 1200px; height: 950px; }

  .card {
    position: absolute; left: 250px; width: 700px; height: 400px;
    overflow: hidden; border-radius: 4px;
    box-shadow: 0 14px 30px rgba(0,0,0,.45);
  }
  .card--front { top: 45px; background: var(--card-white); }
  .card--back {
    top: 505px;
    background: linear-gradient(135deg, var(--card-charcoal-light), var(--card-charcoal) 60%);
  }
  .card__shapes { position: absolute; inset: 0; width: 100%; height: 100%; }

  .holder { position: absolute; right: 50px; top: 72px; text-align: right; color: #fff; }
  .holder__name { font-size: 27px; font-weight: 500; letter-spacing: .3px; }
  .holder__role { font-size: 19px; font-weight: 400; margin-top: 4px; }

  .brand-name {
    color: var(--brand-red); font-weight: 900; text-transform: uppercase;
    line-height: 1; letter-spacing: 1px;
  }
  .card--front .brand-name { position: absolute; left: 48px; top: 150px; font-size: 40px; width: 330px; }

  .contact-row {
    position: absolute; left: 40px; top: 352px;
    display: flex; align-items: center; gap: 14px;
    font-size: 15.5px; color: var(--text-grey);
  }
  .contact-item { display: flex; align-items: center; gap: 6px; white-space: nowrap; }
  .contact-icon { width: 16px; height: 16px; fill: var(--brand-red); flex: none; }

  .card--back .brand-name {
    position: absolute; left: 0; right: 0; top: 150px; text-align: center; font-size: 46px;
  }
  .back-web {
    position: absolute; left: 0; right: 0; top: 225px; text-align: center;
    color: var(--muted-grey); font-size: 19px; letter-spacing: 1.5px;
  }
  .social { position: absolute; right: 24px; top: 22px; display: flex; gap: 5px; }
  .social__box { width: 22px; height: 22px; background: #d9d9d9; border-radius: 2px; }
</style>
</head>
<body>
<main class="canvas">

  <section class="card card--front" aria-label="Business card front">
    <svg class="card__shapes" viewBox="0 0 700 400" preserveAspectRatio="none" aria-hidden="true">
      <path d="M0,0 H700 V378 C610,232 400,52 0,32 Z" fill="var(--stripe-grey)"/>
      <path d="M0,0 H700 V342 C620,202 420,42 0,20 Z" fill="var(--brand-red)"/>
      <path d="M0,0 H700 V120 C560,50 300,10 0,8 Z" fill="var(--brand-red-dark)" opacity=".25"/>
    </svg>

    <div class="holder">
      <p class="holder__name">Teodoro Valbuena</p>
      <p class="holder__role">Producer/Writer/Director</p>
    </div>

    <p class="brand-name">Kestrel Picture House</p>

    <div class="contact-row">
      <span class="contact-item">
        <svg class="contact-icon" viewBox="0 0 16 16" aria-hidden="true"><path d="M3 1h3l1.5 4-2 1.3a9 9 0 0 0 4.2 4.2L11 8.5l4 1.5v3a2 2 0 0 1-2 2A12 12 0 0 1 1 3a2 2 0 0 1 2-2z"/></svg>
        555 014 7789
      </span>
      <span class="contact-item">
        <svg class="contact-icon" viewBox="0 0 16 16" aria-hidden="true"><path d="M1 3h14v10H1z" /><path d="M1 3l7 6 7-6" stroke="#fff" stroke-width="1.3" fill="none"/></svg>
        info@kestrel.example
      </span>
      <span class="contact-item">
        <svg class="contact-icon" viewBox="0 0 16 16" aria-hidden="true"><circle cx="8" cy="8" r="7"/><path d="M1 8h14M8 1c3 3 3 11 0 14M8 1c-3 3-3 11 0 14" stroke="#fff" stroke-width="1" fill="none"/></svg>
        www.kestrelpicturehouse.example
      </span>
    </div>
  </section>

  <section class="card card--back" aria-label="Business card back">
    <div class="social" aria-label="Social profiles">
      <span class="social__box"></span>
      <span class="social__box"></span>
    </div>
    <p class="brand-name">Kestrel Picture House</p>
    <p class="back-web">www.kestrelpicturehouse.example</p>
  </section>

</main>
</body>
</html>
```